Local fast-growing company in the service sector

We are looking for a modern business card design, which should also appear on our letterheads

Target Market(s)

Private and industrial sectors

Contact Information for Business Card

Vorname Name
Kellberger Str. 18
74389 Talbrunnstett
Tel.: 07146-839214-0
Name@agentur-kvtl.de

Colors
9d9d9d
919191
aaaaaa

Requirements
Must have
• The logo (file) in silver

```html
<!DOCTYPE html>
<html lang="de">
<head>
<meta charset="utf-8">
<title>KVTL – Visitenkarte</title>
<link rel="stylesheet" href="https://fonts.googleapis.com/css2?family=Roboto+Condensed:wght@500;700&family=Roboto:wght@400;500&display=swap">
<style>
  :root {
    --stage: #2a2a2c;
    --card: #1b1b1d;
    --silver: #aaaaaa;
    --silver-mid: #9d9d9d;
    --silver-dark: #919191;
    --ink-light: #f2f2f2;
  }
  * { margin: 0; padding: 0; box-sizing: border-box; }
  html, body {
    width: 1200px;
    height: 900px;
    overflow: hidden;
    background: var(--stage);
  }
  .stage {
    width: 1200px;
    height: 900px;
    display: flex;
    flex-direction: column;
    align-items: center;
    justify-content: center;
    gap: 40px;
  }
  .card {
    width: 640px;
    height: 380px;
    background: var(--card);
    position: relative;
    box-shadow: 0 10px 30px rgba(0,0,0,0.45);
  }
  .card-front {
    display: flex;
    flex-direction: column;
    align-items: center;
    justify-content: center;
    gap: 48px;
  }
  .brand {
    display: flex;
    align-items: center;
    gap: 18px;
  }
  .brand-square {
    width: 58px;
    height: 58px;
    background: var(--silver);
  }
  .brand-name {
    font-family: "Roboto Condensed", sans-serif;
    font-weight: 700;
    font-size: 92px;
    line-height: 1;
    letter-spacing: 2px;
    color: var(--silver);
  }
  .front-web {
    font-family: "Roboto", sans-serif;
    font-size: 15px;
    letter-spacing: 9px;
    color: var(--ink-light);
  }
  .identity {
    position: absolute;
    top: 130px;
    left: 56px;
    right: 40px;
    display: flex;
    align-items: center;
  }
  .person-name {
    font-family: "Roboto Condensed", sans-serif;
    font-weight: 700;
    font-size: 36px;
    line-height: 1;
    white-space: nowrap;
    color: var(--silver-mid);
    text-transform: uppercase;
    padding-right: 30px;
  }
  .divider {
    width: 2px;
    height: 96px;
    background: var(--silver-dark);
    margin-right: 30px;
    flex: none;
  }
  .contact-list {
    list-style: none;
    font-family: "Roboto", sans-serif;
    font-size: 17px;
    color: var(--ink-light);
    display: flex;
    flex-direction: column;
    gap: 6px;
    white-space: nowrap;
  }
  .contact-list li,
  .address {
    display: flex;
    align-items: center;
    gap: 12px;
  }
  .icon {
    width: 15px;
    height: 15px;
    fill: var(--silver);
    flex: none;
  }
  .address {
    position: absolute;
    left: 56px;
    bottom: 80px;
    font-family: "Roboto", sans-serif;
    font-size: 18px;
    white-space: nowrap;
    color: var(--ink-light);
  }
</style>
</head>
<body>
<main class="stage">
  <section class="card card-front" aria-label="Vorderseite">
    <div class="brand">
      <span class="brand-square"></span>
      <span class="brand-name">KVTL</span>
    </div>
    <p class="front-web">www.agentur-kvtl.de</p>
  </section>

  <section class="card card-back" aria-label="Rückseite">
    <div class="identity">
      <h1 class="person-name">Lena Hartmann</h1>
      <span class="divider"></span>
      <ul class="contact-list">
        <li>
          <svg class="icon" viewBox="0 0 24 24"><path d="M6.6 10.8a15.1 15.1 0 0 0 6.6 6.6l2.2-2.2a1 1 0 0 1 1-.25 11.4 11.4 0 0 0 3.6.57 1 1 0 0 1 1 1V20a1 1 0 0 1-1 1A17 17 0 0 1 3 4a1 1 0 0 1 1-1h3.5a1 1 0 0 1 1 1 11.4 11.4 0 0 0 .57 3.6 1 1 0 0 1-.25 1z"/></svg>
          07146-839214-0
        </li>
        <li>
          <svg class="icon" viewBox="0 0 24 24"><path d="M2 5h20v14H2z"/><path d="M2 5l10 8 10-8" fill="none" stroke="#1b1b1d" stroke-width="2"/></svg>
          Name@agentur-kvtl.de
        </li>
        <li>
          <svg class="icon" viewBox="0 0 24 24"><circle cx="12" cy="12" r="10"/><path d="M2 12h20M12 2c3 3 3 17 0 20M12 2c-3 3-3 17 0 20" fill="none" stroke="#1b1b1d" stroke-width="1.5"/></svg>
          www.agentur-kvtl.de
        </li>
      </ul>
    </div>
    <p class="address">
      <svg class="icon" viewBox="0 0 24 24"><path d="M12 2a7 7 0 0 0-7 7c0 5 7 13 7 13s7-8 7-13a7 7 0 0 0-7-7zm0 9.5A2.5 2.5 0 1 1 12 6.5a2.5 2.5 0 0 1 0 5z"/></svg>
      Kellberger Str. 18, 74389 Talbrunnstett
    </p>
  </section>
</main>
</body>
</html>
```